Brevard Trade Partners - we are Asian sourcing agents

We are sourcing agents based in the USA and we act as sourcing agents for clients in throughout the world. We focus primarily on custom sewn goods. So basically companies who do not have the in-house expertise to do it themselves, come to us and have us find suitable factories in Asia to do the production. We are middlemen. We find the factories...quote the project...manage the quality control and then deliver the goods directly to our customer's door. We pride ourselves in making the communication very easy and precise.

Current page is www.brevardtradepartners.com

I am not happy w/ the overall look. The spacing...the photos, the fonts...the design elements...the pictures. I want a cool, crisp design that conveys professionalism and clearly depicts/explains what we do.

Requirements
Must have
• use my logo....I like it...it was designed by someone on this website.
Nice to have
• a video/animation of the entire process would be wonderful. Showing initial contact with our office in the USA...then to my correspondence with my offices in Taiwan and in Hong Kong...and then back and fort w/ the customer.....and then between my people in Hong Kong/Taiwan with the local factories......and then a quote is generated and sent to my client......to samples being made and sent for approval.....to a PO being generated......to final samples being sent.....to the order being shipped and delivered to the clients warehouse. I was thinking of an animation showing arrows and text showing the back and forth communication and explaining how the process flows.

```html
<!DOCTYPE html>
<html lang="en">
<head>
<meta charset="utf-8">
<title>Brevard Trade Partners – Asian Sourcing Agents</title>
<link rel="stylesheet" href="https://fonts.googleapis.com/css2?family=Open+Sans:wdth,wght@75..100,400..800&display=swap">
<style>
:root{
  --green:#76941a;
  --green-dark:#6a8616;
  --navy:#1b2f55;
  --ink:#222222;
  --body:#4a4a4a;
  --panel:#f2f2f2;
  --page:#f7f7f7;
  --dark:#121212;
  --darker:#1c1c1c;
  --white:#ffffff;
  --sky-top:#d9e4ef;
  --sky-low:#eef2f6;
}
*{margin:0;padding:0;box-sizing:border-box}
html,body{width:1200px;height:1166px;overflow:hidden}
body{position:relative;background:var(--sky-low);font-family:"Open Sans",Arial,sans-serif;color:var(--body)}
.backdrop{position:absolute;top:0;height:1166px}
.backdrop-left{left:0;width:191px;background:linear-gradient(180deg,#cfdceb 0%,#e9eef4 35%,#2a2f38 70%,#0b0d12 100%)}
.backdrop-right{right:0;width:190px;background:linear-gradient(180deg,#d5e1ee 0%,#e8eef5 45%,#3b5578 75%,#e6ecf2 100%)}
.site{position:absolute;left:191px;top:0;width:819px;height:1166px;background:var(--page)}
.masthead{position:absolute;left:0;top:0;width:819px;height:385px}
.brand-panel{position:absolute;left:0;top:0;width:292px;height:385px;background:var(--panel)}
.brand{position:absolute;left:34px;top:30px;display:flex;align-items:center;gap:10px}
.brand-dot{width:46px;height:46px;border-radius:50%;background:var(--navy)}
.brand-name{font-weight:800;font-stretch:75%;font-size:21px;line-height:1.05;color:var(--navy);width:150px}
.main-nav{position:absolute;left:40px;top:120px;list-style:none}
.main-nav li{height:28.8px;font-weight:700;font-stretch:75%;font-size:14px;color:var(--ink);text-transform:uppercase;letter-spacing:.2px}
.hero{position:absolute;left:292px;top:0;width:527px;height:385px;background:radial-gradient(circle at 30% 45%,#4a8fd6 0%,#1d4f95 35%,#0b2350 75%,#071634 100%)}
.toolbar{position:absolute;left:0;top:385px;width:819px;height:62px;background:var(--green)}
.social{position:absolute;left:25px;top:16px;display:flex;gap:5px}
.social span{width:29px;height:29px;border-radius:50%;background:var(--white)}
.search{position:absolute;left:522px;top:16px;width:175px;height:31px;display:flex;border:1px solid #dfe7cc}
.search-field{flex:1;background:var(--white);font-size:12px;color:#555;line-height:29px;padding-left:9px}
.search-btn{width:36px;background:var(--green-dark);display:flex;align-items:center;justify-content:center}
.account{position:absolute;left:717px;top:23px;font-size:12px;color:var(--white)}
.intro{position:absolute;left:24px;top:486px;width:430px}
.intro h1{font-weight:700;font-stretch:75%;font-size:30px;color:var(--ink);text-transform:uppercase;margin-left:3px;margin-bottom:10px}
.intro p{font-size:12.4px;line-height:22.4px;color:var(--body)}
.benefits{position:absolute;left:495px;top:488px;width:300px}
.benefit h2{font-weight:700;font-stretch:75%;font-size:19px;color:var(--green);text-transform:uppercase;margin-bottom:6px}
.benefit p{font-size:12px;line-height:17px;color:var(--body);width:290px}
.benefit + .benefit{margin-top:27px}
.info-band{position:absolute;left:0;top:820px;width:819px;height:263px}
.know{position:absolute;left:0;top:0;width:332px;height:263px;background:var(--green)}
.know h2{position:absolute;left:24px;top:34px;font-weight:700;font-stretch:75%;font-size:25px;color:var(--white);text-transform:uppercase}
.know ul{position:absolute;left:27px;top:79px;list-style:none}
.know li{font-size:12.6px;line-height:25.6px;color:var(--white)}
.contact-card{position:absolute;left:332px;top:0;width:214px;height:263px;background:var(--dark)}
.advisor{position:absolute;left:54px;top:42px;width:104px;height:104px;border-radius:50%;border:3px solid #d8d8d8;background:linear-gradient(180deg,#c9ccd2,#6c7480)}
.quote-btn{position:absolute;left:20px;top:170px;width:175px;height:50px;border:1px solid var(--white);color:var(--white);font-weight:700;font-stretch:75%;font-size:19px;text-transform:uppercase;display:flex;align-items:center;justify-content:center}
.pitch{position:absolute;left:546px;top:0;width:273px;height:263px;background:var(--darker)}
.pitch h2{position:absolute;left:18px;top:58px;width:250px;font-weight:700;font-stretch:75%;font-size:18.5px;line-height:23.5px;color:var(--white);text-transform:uppercase}
.pitch p{position:absolute;left:17px;top:143px;width:245px;font-size:15.5px;line-height:17px;color:var(--white)}
.site-footer{position:absolute;left:0;top:1083px;width:819px;height:83px;text-align:center;font-size:12px;color:var(--ink);padding-top:30px}
</style>
</head>
<body>
<div class="backdrop backdrop-left" role="img" aria-label="World map backdrop with a businessman silhouette"></div>
<div class="backdrop backdrop-right" role="img" aria-label="World map backdrop with silhouettes of businessmen on phones"></div>

<div class="site">
  <header class="masthead">
    <div class="brand-panel">
      <div class="brand">
        <span class="brand-dot"></span>
        <span class="brand-name">Brevard Trade Partners</span>
      </div>
      <ul class="main-nav">
        <li>Home</li>
        <li>About Us</li>
        <li>Product Categories</li>
        <li>Sourcing &amp; Procurment</li>
        <li>Request Quote</li>
        <li>Clients</li>
        <li>Contact Us</li>
      </ul>
    </div>
    <div class="hero" role="img" aria-label="Hand touching a glowing screen over a world map with the word Outsourcing"></div>
  </header>

  <div class="toolbar">
    <div class="social"><span></span><span></span><span></span><span></span></div>
    <div class="search">
      <div class="search-field">Search Here...</div>
      <div class="search-btn">
        <svg width="16" height="16" viewBox="0 0 16 16"><circle cx="6.5" cy="6.5" r="4.8" fill="none" stroke="#fff" stroke-width="1.8"/><line x1="10" y1="10" x2="14.5" y2="14.5" stroke="#fff" stroke-width="2" stroke-linecap="round"/></svg>
      </div>
    </div>
    <div class="account">Login /&nbsp; Register</div>
  </div>

  <section class="intro">
    <h1>Brevard Trade Partners</h1>
    <p>Lorem ipsum dolor sit amet, consectetur adipiscing elit. Praesent at tincidunt dolor, nec pulvinar elit. Vivamus imperdiet ipsum lacus, eu suscipit lacus maximus sed. Donec a posuere magna. Fusce finibus, elit nec semper convallis, odio magna feugiat nibh, eget feugiat elit nunc eu erat. Vestibulum ante ipsum primis in faucibus orci luctus et ultrices posuere cubilia Curae; Aliquam ac ipsum in mi luctus bibendum ac vitae nibh. Cras malesuada consequat dui, efficitur ultrices lectus aliquam ut. Nulla congue sollicitudin suscipit. Phasellus luctus fringilla diam convallis elementum. Curabitur quis lobortis est. Proin venenatis luctus efficitur. Nam tempor mattis nibh, id hendrerit felis malesuada ac. Aliquam sit amet urna eu nulla eleifend bibendum sed ut est. Mauris tempus sodales nibh, eget scelerisque sem viverra sed.</p>
  </section>

  <section class="benefits">
    <div class="benefit">
      <h2>Access Emerging Markets</h2>
      <p>Lorem ipsum dolor sit amet, consectetur adipiscing elit. Praesent at tincidunt dolor, nec pulvinar elit. Vivamus imperdiet ipsum lacus, maximus sed.</p>
    </div>
    <div class="benefit">
      <h2>Realise Value by Sourcing Direct</h2>
      <p>Lorem ipsum dolor sit amet, consectetur adipiscing elit. Praesent at tincidunt dolor, nec pulvinar elit. Vivamus imperdiet ipsum lacus, maximus sed.</p>
    </div>
    <div class="benefit">
      <h2>Manage Quality and Reliability Risks</h2>
      <p>Lorem ipsum dolor sit amet, consectetur adipiscing elit. Praesent at tincidunt dolor, nec pulvinar elit. Vivamus imperdiet ipsum lacus, maximus sed.</p>
    </div>
  </section>

  <section class="info-band">
    <div class="know">
      <h2>What Do You Need to Know</h2>
      <ul>
        <li>Contract Sewing in China</li>
        <li>What is the Process?</li>
        <li>What the Minimum Order?</li>
        <li>Contract Outsourcing FAQ</li>
        <li>Outsourcing Case Study</li>
        <li>Custom Industrial Sewing in China</li>
      </ul>
    </div>
    <div class="contact-card">
      <div class="advisor" role="img" aria-label="Portrait of a smiling sourcing advisor in a suit"></div>
      <div class="quote-btn">Request Quote</div>
    </div>
    <div class="pitch">
      <h2>Outsource your sewing needs to trusted contractors in China</h2>
      <p>Please contact us for immediate consultation regarding your outsourcing project.</p>
    </div>
  </section>

  <footer class="site-footer">© Copyright 2015, Brevard Trade Partners, LLC. All rights reserved.</footer>
</div>
</body>
</html>
```